Business card design for Virtual Assistance company

I need a business card designed for my virtual assistance company. We are a small company who services primarily C-level executive clients. The card needs to be double sided with the following contact information on the back:
Melissa Thornbury
Owner/CEO
info@rkpadvisory.net
www.rkpadvisory.net
555.302.9817

The front side should just have the company name incorporated: "RKP Advisory" and "virtual assistance"

The card should be simplistic, but eye catching and should speak to high level executives. Our primary focus areas consist of executive assistance and government contracting.

Target Market(s)

CEOs and executives

Contact Information for Business Card

see project description. phone, email, website.

Colors

Designer to choose only greyscale colors for use in the design.

```html
<!DOCTYPE html>
<html lang="en">
<head>
<meta charset="UTF-8">
<title>RKP Advisory – Business Card</title>
<link href="https://fonts.googleapis.com/css2?family=Cinzel:wght@500;600&family=Poppins:wght@300;400&display=swap" rel="stylesheet">
<style>
  :root {
    --ink: #2b2b2b;
    --ink-light: #4a4a4a;
    --ink-dark: #1a1a1a;
    --white: #ffffff;
    --grey-band: #a3a3a3;
    --grey-text: #8a8a8a;
    --backdrop: #b4b4b4;
    --backdrop-edge: #8a8a8a;
  }
  * { margin: 0; padding: 0; box-sizing: border-box; }
  html, body { width: 1200px; height: 1015px; overflow: hidden; }
  body {
    background: radial-gradient(ellipse at 50% 40%, var(--backdrop) 0%, var(--backdrop-edge) 100%);
    position: relative;
    font-family: "Poppins", sans-serif;
  }
  .card {
    position: absolute;
    width: 560px;
    height: 320px;
    box-shadow: 0 10px 26px rgba(0,0,0,0.35);
    overflow: hidden;
  }
  .card-back { left: 130px; top: 120px; }
  .card-front { left: 510px; top: 570px; background: var(--ink); }

  .back-pattern {
    position: absolute; inset: 0;
    background: linear-gradient(160deg, var(--ink-light) 0%, var(--ink) 50%, var(--ink-dark) 100%);
  }
  .back-mark {
    position: absolute;
    right: 96px; top: 176px;
    font-family: "Cinzel", serif;
    font-weight: 600;
    font-size: 22px;
    letter-spacing: 1px;
    color: var(--white);
  }

  .front-shapes { position: absolute; inset: 0; }
  .brand {
    position: absolute;
    right: 34px; top: 50px;
    width: 300px;
    text-align: center;
  }
  .brand-name {
    font-family: "Cinzel", serif;
    font-weight: 600;
    font-size: 34px;
    color: var(--ink);
    line-height: 1.1;
    white-space: nowrap;
  }
  .brand-tagline {
    display: flex; align-items: center; justify-content: center; gap: 8px;
    margin-top: 6px;
    font-weight: 400;
    font-size: 10px;
    letter-spacing: 2.5px;
    color: var(--grey-text);
  }
  .brand-tagline::before, .brand-tagline::after {
    content: ""; width: 26px; height: 1px; background: var(--grey-text);
  }

  .contact-block {
    position: absolute;
    left: 42px; top: 172px;
    color: var(--white);
  }
  .person-name {
    font-family: "Cinzel", serif;
    font-weight: 500;
    font-size: 18px;
    letter-spacing: 0.5px;
  }
  .person-title {
    font-weight: 300;
    font-size: 13px;
    margin-top: 1px;
  }
  .divider { width: 40px; height: 1px; background: var(--white); margin: 8px 0 22px; }
  .contact-list { list-style: none; }
  .contact-list li {
    display: flex; align-items: center; gap: 8px;
    font-weight: 300;
    font-size: 14px;
    line-height: 20px;
  }
  .contact-list svg { width: 13px; height: 13px; flex: none; }
</style>
</head>
<body>

  <section class="card card-back" aria-label="Card back">
    <div class="back-pattern" role="img" aria-label="Repeating embossed brand-initials pattern on charcoal"></div>
    <div class="back-mark">RKP</div>
  </section>

  <section class="card card-front" aria-label="Card front">
    <svg class="front-shapes" viewBox="0 0 560 320" preserveAspectRatio="none">
      <path d="M168 0 C 200 175, 380 235, 560 195 L560 0 Z" fill="var(--grey-band)"/>
      <path d="M192 0 C 226 160, 392 215, 560 182 L560 0 Z" fill="var(--white)"/>
    </svg>

    <div class="brand">
      <div class="brand-name">RKP Advisory</div>
      <div class="brand-tagline">VIRTUAL ASSISTANCE</div>
    </div>

    <div class="contact-block">
      <div class="person-name">MELISSA THORNBURY</div>
      <div class="person-title">Owner/CEO</div>
      <div class="divider"></div>
      <ul class="contact-list">
        <li>
          <svg viewBox="0 0 24 24" fill="var(--white)"><path d="M6.6 10.8a15.1 15.1 0 0 0 6.6 6.6l2.2-2.2c.3-.3.7-.4 1-.2 1.1.4 2.3.6 3.6.6.6 0 1 .4 1 1V20c0 .6-.4 1-1 1A17 17 0 0 1 3 4c0-.6.4-1 1-1h3.5c.6 0 1 .4 1 1 0 1.3.2 2.5.6 3.6.1.3 0 .7-.2 1z"/></svg>
          555.302.9817
        </li>
        <li>
          <svg viewBox="0 0 24 24" fill="none" stroke="var(--white)" stroke-width="2"><rect x="3" y="5" width="18" height="14"/><path d="M3 5l9 8 9-8"/></svg>
          info@rkpadvisory.net
        </li>
        <li>
          <svg viewBox="0 0 24 24" fill="none" stroke="var(--white)" stroke-width="2"><circle cx="12" cy="12" r="9"/><ellipse cx="12" cy="12" rx="4" ry="9"/><path d="M3 12h18"/></svg>
          www.rkpadvisory.net
        </li>
      </ul>
    </div>
  </section>

</body>
</html>
```